Harbor Loom Floors Letterhead

Letterhead used for business reasons. It must be editable and easy to use.

Address is 2715 W. Pelican Lane Brookhaven ME 34187 - 555.382.6519

```html
<!DOCTYPE html>
<html lang="en">
<head>
<meta charset="UTF-8">
<title>Harbor Loom Floors Letterhead</title>
<link rel="stylesheet" href="https://fonts.googleapis.com/css2?family=Lato:wght@400;700&family=Montserrat:wght@400&family=Satisfy&family=Dancing+Script:wght@500&display=swap">
<style>
  :root {
    --backdrop: #e6e6e8;
    --paper: #ffffff;
    --ink: #1d1d1d;
    --ink-soft: #444444;
    --accent: #e0902a;
  }
  * { box-sizing: border-box; margin: 0; padding: 0; }
  html, body {
    width: 1200px;
    height: 874px;
    overflow: hidden;
    background: var(--backdrop);
  }
  .letterhead {
    position: absolute;
    left: 300px;
    top: 14px;
    width: 600px;
    height: 846px;
    background: var(--paper);
    box-shadow: 0 2px 10px rgba(0,0,0,0.12);
    font-family: "Lato", sans-serif;
    color: var(--ink);
  }
  .letterhead__contact {
    position: absolute;
    top: 48px;
    right: 52px;
    display: flex;
    align-items: center;
    gap: 14px;
    font-family: "Montserrat", sans-serif;
    font-size: 8.5px;
    line-height: 1.35;
    color: var(--ink-soft);
  }
  .contact__address { font-style: normal; }
  .contact__divider {
    width: 1px;
    height: 26px;
    background: var(--accent);
  }
  .contact__phone {
    display: flex;
    align-items: center;
    gap: 5px;
  }
  .brand-name {
    position: absolute;
    top: 108px;
    left: 56px;
    font-family: "Lato", sans-serif;
    font-weight: 400;
    font-size: 24px;
    color: var(--accent);
    letter-spacing: 0.5px;
  }
  .letter {
    position: absolute;
    top: 170px;
    left: 68px;
    right: 52px;
    font-size: 10.5px;
    line-height: 1.38;
  }
  .letter__date { margin-bottom: 12px; }
  .letter__recipient { margin-bottom: 12px; }
  .letter__salutation {
    font-weight: 700;
    font-size: 13px;
    margin: 16px 0 18px;
  }
  .letter__body p { margin-bottom: 14px; }
  .letter__closing { margin-top: 22px; }
  .letter__signature {
    font-family: "Satisfy", "Dancing Script", cursive;
    font-size: 28px;
    line-height: 1.2;
    margin: 26px 0 0 46px;
  }
</style>
</head>
<body>
  <main class="letterhead">
    <header>
      <div class="brand-name">Harbor Loom Floors</div>
      <div class="letterhead__contact">
        <address class="contact__address">
          2715 W. Pelican Lane<br>Brookhaven ME 34187
        </address>
        <span class="contact__divider"></span>
        <span class="contact__phone">
          <svg width="8" height="8" viewBox="0 0 24 24" aria-hidden="true">
            <path fill="#e0902a" d="M6.6 10.8a15.1 15.1 0 0 0 6.6 6.6l2.2-2.2c.3-.3.7-.4 1-.2 1.1.4 2.3.6 3.6.6.6 0 1 .4 1 1V20c0 .6-.4 1-1 1C10.6 21 3 13.4 3 4c0-.6.4-1 1-1h3.5c.6 0 1 .4 1 1 0 1.3.2 2.5.6 3.6.1.3 0 .7-.2 1z"/>
          </svg>
          555.382.6519
        </span>
      </div>
    </header>

    <article class="letter">
      <p class="letter__date">January-03-2020</p>
      <p class="letter__recipient">Mr. Daniel Reyes<br>President</p>
      <p class="letter__recipient">Crestline Corporation<br>123 Street Name, Suite# 10<br>City, State, 120023</p>
      <p class="letter__salutation">Dear Mr. Daniel</p>
      <div class="letter__body">
        <p>Lorem ipsum dolor sit amet, consectetur adipiscing elit, sed do eiusmod tempor incididunt ut labore et dolore magna aliqua. Ut enim ad minim veniam, quis nostrud exercitation ullamco laboris nisi ut aliquip ex ea commodo consequat. Duis aute irure dolor in reprehenderit in voluptate velit esse cillum dolore eu fugiat nulla pariatur.</p>
        <p>Lorem ipsum dolor sit amet, consectetur adipiscing elit, sed do eiusmod tempor incididunt ut labore et dolore magna aliqua. Ut enim ad minim veniam, quis nostrud exercitation ullamco laboris nisi ut aliquip ex ea commodo consequat. Duis aute irure dolor in reprehenderit in voluptate velit esse cillum dolore eu fugiat nulla pariatur.</p>
        <p>Lorem ipsum dolor sit amet, consectetur adipiscing elit, sed do eiusmod tempor incididunt ut labore et dolore magna aliqua. Ut enim ad minim veniam, quis nostrud exercitation ullamco laboris nisi ut aliquip ex ea commodo consequat.</p>
        <p>Excepteur sint occaecat cupidatat non proident, sunt in culpa qui officia deserunt mollit anim id est laborum. re et dolore magnam aliquam quaerat voluptatem.</p>
      </div>
      <p class="letter__closing">Regards</p>
      <p class="letter__signature">Marian Holt</p>
    </article>
  </main>
</body>
</html>
```